Website Design - TallyPorchHelpers.net

PLEASE CHECK WORD DOCUMENT ATTACHED FOR WEBSITE FLOW.

Target Market(s)

REAL ESTATE AGENTS ARE THE TARGET MARKET

Industry/Entity Type

Real Estate

Coding

Coded - Design and coding required

Number of Pages Required

4 page

Colors

Designer to choose colors to be used in the design.

Requirements
Must have
• WE LIKE RED LOGO ATTACHED
Nice to have
• PLEASE CHECK WORD DOCUMENT ATTACHED FOR WEBSITE FLOW.
Should not have

```html
<!DOCTYPE html>
<html lang="en">
<head>
<meta charset="utf-8">
<title>TallyPorchHelpers.net</title>
<link rel="stylesheet" href="https://fonts.googleapis.com/css2?family=Roboto+Condensed:wght@400;700&family=Open+Sans:wght@400;600;700&display=swap">
<style>
:root{
  --red:#d6151b;
  --blue:#1d4aa8;
  --blue-dark:#163a86;
  --navy:#121a2c;
  --navy-deep:#0c1220;
  --ink:#2b2b2b;
  --muted:#555;
  --light:#f0f0f0;
  --white:#fff;
}
*{box-sizing:border-box;margin:0;padding:0}
html,body{width:1200px;height:4986px;overflow:hidden}
body{font-family:"Open Sans",sans-serif;color:var(--ink);background:var(--white);position:relative}
.heading{font-family:"Roboto Condensed",sans-serif;font-weight:400;text-transform:uppercase;text-align:center;font-size:34px;letter-spacing:.5px}
section,header,footer,.bottom-bar{position:absolute;left:0;width:1200px}

/* header */
.site-header{top:0;height:126px;background:var(--white)}
.brand{position:absolute;left:90px;top:38px;display:flex;align-items:center;gap:12px;font-weight:700;font-size:22px;color:var(--red)}
.brand-square{width:34px;height:34px;background:var(--red)}
.call{position:absolute;right:90px;top:26px;font-size:15px;color:var(--ink);display:flex;align-items:center;gap:8px}
.nav{position:absolute;right:90px;top:72px;display:flex;gap:38px;font-size:15px}

/* hero */
.hero{top:126px;height:512px;background:linear-gradient(180deg,#6f8fb5 0%,#8fa6b8 35%,#5d7a45 65%,#3f6a2c 100%)}
.hero-tagline{position:absolute;right:90px;top:196px;width:560px;text-align:right;color:var(--white);font-size:24px;line-height:36px;text-shadow:0 1px 3px rgba(0,0,0,.5)}

/* choose */
.choose{top:638px;height:243px;background:linear-gradient(180deg,var(--blue) 0%,var(--blue-dark) 100%)}
.choose .heading{color:var(--white);margin-top:56px;font-size:30px}
.choose-options{display:flex;justify-content:center;gap:22px;margin-top:44px}
.option{background:var(--white);color:var(--ink);font-family:"Roboto Condensed",sans-serif;text-transform:uppercase;font-size:16px;height:48px;display:flex;align-items:center;padding:0 30px;border-radius:2px}

/* how it works */
.how{top:881px;height:559px}
.how .heading{margin-top:88px}
.step{position:absolute;top:183px;width:322px;height:272px;text-align:center;font-size:15px;line-height:23px;color:var(--muted);padding:0 20px}
.step.featured{box-shadow:0 0 10px rgba(0,0,0,.25);background:var(--white)}
.step-icon{width:92px;height:92px;border-radius:50%;background:var(--red);margin:24px auto 28px;position:relative;display:flex;align-items:center;justify-content:center}
.step-num{position:absolute;right:-8px;top:-4px;width:28px;height:28px;border-radius:50%;background:var(--white);border:2px solid var(--red);color:var(--red);font-size:13px;display:flex;align-items:center;justify-content:center}

/* pricing */
.pricing{top:1440px;height:770px;background:linear-gradient(180deg,#3a3f47 0%,#2a2e35 100%)}
.pricing .heading{color:var(--white);margin-top:80px}
.plan{position:absolute;top:192px;height:382px;background:var(--white);text-align:center}
.plan-name{height:36px;line-height:36px;font-size:17px;font-family:"Roboto Condensed",sans-serif}
.plan-band{height:60px;background:var(--blue);position:relative;color:var(--white);font-size:13px;font-weight:700;line-height:18px;padding-top:12px}
.price{width:84px;height:84px;border-radius:50%;background:var(--blue);border:4px solid var(--white);color:var(--white);position:absolute;left:50%;top:8px;transform:translateX(-50%);display:flex;align-items:center;justify-content:center;font-size:24px;font-family:"Roboto Condensed",sans-serif}
.plan ol{list-style:none;font-size:12px;line-height:16px;color:var(--muted);padding:44px 18px 0}
.plan li{margin-bottom:8px}
.plan.custom ol{padding-top:20px}
.buy{position:absolute;bottom:26px;left:0;right:0;color:var(--blue);font-size:12px;font-weight:700}
.btn{position:absolute;background:var(--red);color:var(--white);font-family:"Roboto Condensed",sans-serif;text-transform:uppercase;font-size:17px;display:flex;align-items:center;justify-content:center;border-radius:3px}

/* subscription */
.subscribe{top:2210px;height:758px;background:var(--light)}
.subscribe .heading{margin-top:108px;line-height:50px;color:#222}
.service{position:absolute;top:292px;width:230px;text-align:center}
.service-icon{width:114px;height:114px;border-radius:50%;background:var(--white);border:3px solid var(--red);margin:0 auto 28px;display:flex;align-items:center;justify-content:center}
.service h3{font-family:"Roboto Condensed",sans-serif;font-size:19px;margin-bottom:12px;color:#222}
.service p{font-size:14px;line-height:23px;color:var(--muted)}

/* service area */
.area{top:2968px;height:672px;background:linear-gradient(180deg,#2b5ab8 0%,#1c3f8c 100%)}
.area .heading{color:var(--white);margin-top:64px}
.map-frame{position:absolute;left:90px;top:147px;width:1020px;height:468px;background:var(--white);border:4px solid #ddd}
.map-search{height:54px;background:#e2e2e2;display:flex;align-items:center;gap:10px;padding-left:20px;font-size:15px;color:#333}
.map{height:406px;background:linear-gradient(135deg,#e9e6df 0%,#dcd8cc 45%,#a9cbe6 60%,#b6d3ea 100%)}

/* faq */
.faq{top:3640px;height:698px}
.faq .heading{margin-top:72px}
.faq-item{position:absolute;left:173px;width:857px;height:87px;background:var(--white);border:1px solid #ddd;border-left:6px solid var(--red);box-shadow:0 1px 4px rgba(0,0,0,.15);padding:14px 30px}
.faq-item h4{font-weight:400;font-size:17px;margin-bottom:8px}
.faq-item p{font-size:13px;color:var(--muted)}

/* testimonial */
.quote{top:4338px;height:223px;background:linear-gradient(180deg,#2a2d33,#1e2126)}
.quote-mark{position:absolute;left:568px;top:-22px;width:64px;height:64px;border-radius:50%;background:var(--red);display:flex;align-items:center;justify-content:center}
.quote-text{position:absolute;left:150px;width:900px;top:88px;text-align:center;color:var(--white);font-size:15px;line-height:32px}
.quote-author{position:absolute;left:0;width:1200px;top:166px;text-align:center;color:#ccc;font-size:14px;font-style:italic}

/* footer */
.site-footer{top:4561px;height:352px;background:var(--navy)}
.foot-col{position:absolute;top:86px;color:var(--white)}
.foot-col h5{font-family:"Roboto Condensed",sans-serif;font-weight:400;text-transform:uppercase;font-size:22px;margin-bottom:20px}
.foot-col p{font-size:14px;line-height:24px}
.contact-line{display:flex;gap:14px;margin-bottom:22px;font-size:14px;line-height:22px}
.contact-line strong{display:block;font-size:14px}
.form{display:grid;grid-template-columns:1fr 1fr;gap:10px;width:300px}
.field{height:34px;background:var(--white);color:#555;font-size:13px;padding:8px 10px}
.field.wide{grid-column:1/3}
.submit{width:104px;height:30px;background:var(--red);color:var(--white);font-size:14px;display:flex;align-items:center;justify-content:center}
.bottom-bar{top:4913px;height:73px;background:var(--navy-deep);color:#ccc;font-size:13px;text-align:center;line-height:73px}
</style>
</head>
<body>

<header class="site-header">
  <div class="brand"><span class="brand-square"></span>TallyPorchHelpers.net</div>
  <div class="call">
    <svg width="22" height="22" viewBox="0 0 24 24"><circle cx="12" cy="12" r="12" fill="#d6151b"/><path d="M8 6l2 3-1.2 1.4a8 8 0 0 0 4.8 4.8L15 14l3 2-1 2.3C11 18 6 13 5.7 7z" fill="#fff"/></svg>
    Call Or Text Us 1-555-014-0196
  </div>
  <nav class="nav"><span>How it works</span><span>Service</span><span>Pricing</span><span>About us</span><span>Faq</span><span>Contact</span></nav>
</header>

<section class="hero" role="img" aria-label="Suburban house with an open house yard sign on the lawn">
  <p class="hero-tagline">Helping agents save time and money. We place signs and boost foot traffic to your open houses using proven marketing techniques.</p>
</section>

<section class="choose">
  <h2 class="heading">Choose the option below that best describes you</h2>
  <div class="choose-options">
    <span class="option">I'm a full on brokerage</span>
    <span class="option">I'm an ind. broker with a team</span>
    <span class="option">I need sign placement asap</span>
  </div>
</section>

<section class="how">
  <h2 class="heading">How it works</h2>
  <div class="step" style="left:88px">
    <div class="step-icon"><span class="step-num">1</span>
      <svg width="40" height="48" viewBox="0 0 40 48"><path d="M20 2a16 16 0 0 0-16 16c0 12 16 28 16 28s16-16 16-28A16 16 0 0 0 20 2z" fill="none" stroke="#fff" stroke-width="3"/><circle cx="20" cy="18" r="6" fill="#fff"/></svg>
    </div>
    We boost Foot Traffic To Your Open House Using Proven Marketing Channels, Social Feed Ads, SMS Notifications, Voice Broadcasts and Email Notifications
  </div>
  <div class="step featured" style="left:449px">
    <div class="step-icon"><span class="step-num">2</span>
      <svg width="48" height="44" viewBox="0 0 48 44"><path d="M4 22L24 4l20 18" fill="none" stroke="#fff" stroke-width="3"/><rect x="10" y="20" width="28" height="22" fill="none" stroke="#fff" stroke-width="3"/><rect x="20" y="28" width="8" height="14" fill="#fff"/></svg>
    </div>
    We Place Open House Signs Strategically In The Surrounding Area
  </div>
  <div class="step" style="left:800px">
    <div class="step-icon"><span class="step-num">3</span>
      <svg width="48" height="44" viewBox="0 0 48 44"><rect x="4" y="6" width="40" height="22" rx="2" fill="none" stroke="#fff" stroke-width="3"/><path d="M14 28v14M34 28v14" stroke="#fff" stroke-width="3"/><path d="M12 17h24" stroke="#fff" stroke-width="3"/></svg>
    </div>
    We Pick Up The Signs Once Your Open House Ends
  </div>
</section>

<section class="pricing" aria-label="Pricing package">
  <h2 class="heading">Pricing package</h2>
  <div class="plan" style="left:83px;width:183px">
    <div class="plan-name">5 Signs</div><div class="plan-band"><span class="price">$49</span></div>
    <ol><li>1. Place signs strategically in best areas according to where the open house is located</li><li>2. Pick Up the signs after the open house</li><li>3. Store custom signs for you if needed</li></ol>
    <span class="buy">BUY NOW »</span>
  </div>
  <div class="plan" style="left:292px;width:183px">
    <div class="plan-name">10 Signs</div><div class="plan-band"><span class="price">$59</span></div>
    <ol><li>1. Place signs strategically in best areas according to where the open house is located</li><li>2. Pick Up the signs after the open house</li><li>3. Store custom signs for you if needed</li></ol>
    <span class="buy">BUY NOW »</span>
  </div>
  <div class="plan" style="left:502px;width:183px">
    <div class="plan-name">15 Signs</div><div class="plan-band"><span class="price">$69</span></div>
    <ol><li>1. Place signs strategically in best areas according to where the open house is located</li><li>2. Pick Up the signs after the open house</li><li>3. Store custom signs for you if needed</li></ol>
    <span class="buy">BUY NOW »</span>
  </div>
  <div class="plan" style="left:708px;width:183px">
    <div class="plan-name">20 Signs</div><div class="plan-band"><span class="price">$79</span></div>
    <ol><li>1. Place signs strategically in best areas according to where the open house is located</li><li>2. Pick Up the signs after the open house</li><li>3. Store custom signs for you if needed</li></ol>
    <span class="buy">BUY NOW »</span>
  </div>
  <div class="plan custom" style="left:917px;width:200px">
    <div class="plan-name">25+ Signs</div><div class="plan-band">Click Buy Now<br>To Create Custom Pkg.</div>
    <ol><li>1. Place signs strategically in best areas according to where the open house is located</li><li>2. Pick Up the signs after the open house</li><li>3. Store custom signs for you if needed</li></ol>
    <span class="buy">BUY NOW »</span>
  </div>
  <span class="btn" style="left:465px;top:628px;width:270px;height:50px">Subscribe to email list</span>
</section>

<section class="subscribe">
  <h2 class="heading">Sign up for a subscription and get these<br>marketing services for free</h2>
  <div class="service" style="left:72px">
    <div class="service-icon"><svg width="50" height="46" viewBox="0 0 50 46"><path d="M4 4h42v28H20l-10 10V32H4z" fill="none" stroke="#d6151b" stroke-width="3"/><circle cx="16" cy="18" r="2.5" fill="#d6151b"/><circle cx="25" cy="18" r="2.5" fill="#d6151b"/><circle cx="34" cy="18" r="2.5" fill="#d6151b"/></svg></div>
    <h3>SMS</h3><p>Send sms blast to your neigh-borhood informing them your home is for sale and if they know anyone looking to send them over</p>
  </div>
  <div class="service" style="left:345px">
    <div class="service-icon"><svg width="56" height="40" viewBox="0 0 56 40"><rect x="3" y="3" width="50" height="34" fill="none" stroke="#d6151b" stroke-width="3"/><path d="M3 3l25 20L53 3" fill="none" stroke="#d6151b" stroke-width="3"/></svg></div>
    <h3>EMAIL</h3><p>Email blast to your neighbor-hood informing them your home is for sale and if they know anyone looking to send them over</p>
  </div>
  <div class="service" style="left:618px">
    <div class="service-icon"><svg width="48" height="44" viewBox="0 0 48 44"><rect x="3" y="3" width="42" height="38" rx="3" fill="none" stroke="#d6151b" stroke-width="3"/><path d="M10 14h28M10 22h28M10 30h16" stroke="#d6151b" stroke-width="3"/></svg></div>
    <h3>SOCIAL AD</h3><p>Newsfeed ads to people in your open house area</p>
  </div>
  <div class="service" style="left:891px">
    <div class="service-icon"><svg width="48" height="48" viewBox="0 0 48 48"><path d="M26 4h18v18L22 44 4 26z" fill="none" stroke="#d6151b" stroke-width="3"/><circle cx="36" cy="12" r="3" fill="#d6151b"/></svg></div>
    <h3>VB</h3><p>VB blast to your neighbor-hood informing them your home is for sale and if they know anyone looking to send them over</p>
  </div>
  <span class="btn" style="left:540px;top:615px;width:120px;height:48px">Sign up</span>
</section>

<section class="area">
  <h2 class="heading">Service area</h2>
  <div class="map-frame">
    <div class="map-search">
      <svg width="16" height="20" viewBox="0 0 16 20"><path d="M8 1a7 7 0 0 0-7 7c0 5 7 11 7 11s7-6 7-11a7 7 0 0 0-7-7z" fill="#333"/><circle cx="8" cy="8" r="2.5" fill="#e2e2e2"/></svg>
      Enter Your Open House Address To See If We Service It
    </div>
    <div class="map" role="img" aria-label="Street map of the coastal service area with a location marker"></div>
  </div>
</section>

<section class="faq">
  <h2 class="heading">FAQ</h2>
  <div class="faq-item" style="top:169px"><h4>Q- Why choose Porchlight Crew?</h4><p>A- It is a long established fact that a reader will be distracted by the readable content of a page.</p></div>
  <div class="faq-item" style="top:272px"><h4>Q- quisquam est qui dolorem ipsum quia dolor sit amet?</h4><p>A- The point of using Lorem Ipsum is that it has a more-or-less normal distribution of letters, as opposed</p></div>
  <div class="faq-item" style="top:375px"><h4>Q- Neque porro quisquam est qui dolorem ipsum quia dolor sit amet?</h4><p>A- Lorem Ipsum as their default model text, and a search for 'lorem ipsum' will uncover many web sites.</p></div>
  <div class="faq-item" style="top:478px"><h4>Q- Porro quisquam est qui dolorem ipsum quia dolor sit amet, consectetur?</h4><p>A- Various versions have evolved over the years, sometimes by accident, sometimes on purpose</p></div>
</section>

<section class="quote">
  <div class="quote-mark"><svg width="28" height="22" viewBox="0 0 28 22"><path d="M2 22V12C2 5 6 1 12 0v4C8 5 7 8 7 11h5v11zM16 22V12c0-7 4-11 10-12v4c-4 1-5 4-5 7h5v11z" fill="#fff"/></svg></div>
  <p class="quote-text">The point of using Lorem Ipsum is that it has a more-or-less normal distribution of letters, as opposed to using 'Content here, content here', making it look like readable English Many desktop publishing packages and web page editors now</p>
  <p class="quote-author">Neque porro quisquam</p>
</section>

<footer class="site-footer">
  <div class="foot-col" style="left:90px;width:330px">
    <h5>About us</h5>
    <p>Owned and operated by a Highly Experienced and Skilled Promoter, An Expert Marketer and a Savvy Realtor, we help agents leverage their time and skills to increase production at an affordable price with impeccable support!</p>
  </div>
  <div class="foot-col" style="left:515px;width:270px">
    <h5>Contact us</h5>
    <div class="contact-line">
      <svg width="18" height="22" viewBox="0 0 18 22"><path d="M9 1a8 8 0 0 0-8 8c0 6 8 12 8 12s8-6 8-12a8 8 0 0 0-8-8z" fill="none" stroke="#fff" stroke-width="2"/><circle cx="9" cy="9" r="2.5" fill="#fff"/></svg>
      <div><strong>ADDRESS</strong>48 Larkspur Avenue, Suite 2<br>Fernvale, NC 27000</div>
    </div>
    <div class="contact-line">
      <svg width="18" height="20" viewBox="0 0 24 24"><path d="M6 2l4 5-2 2a11 11 0 0 0 7 7l2-2 5 4-2 4C10 22 2 14 2 4z" fill="none" stroke="#fff" stroke-width="2"/></svg>
      <div><strong>PHONE NUMBER</strong>1-555-014-0196</div>
    </div>
  </div>
  <div class="foot-col" style="left:810px">
    <h5>Contact form</h5>
    <div class="form">
      <span class="field">Name</span><span class="field">Cell Phone</span>
      <span class="field wide">Email</span>
      <span class="field wide">Message</span>
      <span class="submit">Submit</span>
    </div>
  </div>
</footer>
<div class="bottom-bar">© 2018 Company Name. All right reserved</div>

</body>
</html>
```